Nutrition business needs logo & business card design

We need a business card & logo design for a new company based in Toronto, Ontario Canada called Verdel Wellworks.

We provide nutrition service using metrics as guide to manage client's progress. Our service creates individualized nutrition and lifestyle strategies that focuses on improving Performance, Longevity and Weight Loss. I would like to see designs that use the color of green, gray, blue and white.

The final design should:

--convey a feeling of connectedness with positive transformation.

-- communicate the idea of awareness with guided effort that yields personal independence for a better and more productive life

Target Market(s)

Professionals who work in the IT/Computer/Engineering/Banking industry specifically Directors, Managers, CEO's.

Industry/Entity Type

Health And Wellness

Contact Information for Business Card

Dorvane Pike, Owner
email: DPIKE@verdelwellworks.example
tel: - 555-204-7718

Logo Text

better health through analytics or measure to manage

Font styles to use
Other font styles liked:
• Garamound

Colors
ffffff
abd037
85acd3
757575
34a7d7

Requirements
Must have
• Good contrast and decent size font - ease of readability, aesthetically nice colors
Nice to have
• image of chart or graph that conveys measurement or analytics
Should not have
• Borders, images of food,

```html
<!DOCTYPE html>
<html lang="en">
<head>
<meta charset="utf-8">
<title>Verdel Wellworks — Business Card</title>
<link rel="stylesheet" href="https://fonts.googleapis.com/css2?family=Lato:wght@300;400;700&display=swap">
<style>
  :root {
    --brand-blue: #0b86f2;
    --brand-green: #3aa61c;
    --paper: #ffffff;
    --paper-shade: #f1f1f1;
    --backdrop: #e9e6e1;
    --ink-light: #ffffff;
  }
  * { box-sizing: border-box; margin: 0; padding: 0; }
  html, body {
    width: 1200px; height: 900px; overflow: hidden;
    background: var(--backdrop);
    font-family: "Lato", Arial, sans-serif;
  }
  .canvas {
    position: relative; width: 1200px; height: 900px;
  }
  .card {
    position: absolute; width: 540px; height: 308px;
    overflow: hidden;
    box-shadow: 0 6px 18px rgba(0,0,0,0.18);
  }
  /* Front */
  .card-front {
    left: 40px; top: 296px;
    background: var(--brand-blue);
    display: flex; align-items: center; justify-content: center; gap: 22px;
  }
  .card-front .mark-circle {
    width: 112px; height: 112px; border-radius: 50%;
    border: 6px solid var(--ink-light);
  }
  .card-front .wordmark {
    color: var(--ink-light); font-weight: 300; font-size: 40px; letter-spacing: -0.5px;
  }
  /* Back */
  .card-back {
    left: 620px; top: 296px;
    background: var(--paper);
  }
  .card-back .header {
    position: absolute; left: 0; top: 0; width: 100%; height: 138px;
    background: linear-gradient(180deg, var(--paper) 0%, var(--paper-shade) 100%);
    display: flex; align-items: center; justify-content: center; gap: 16px;
    border-bottom: 4px solid var(--brand-green);
  }
  .card-back .mark-circle {
    width: 90px; height: 90px; border-radius: 50%;
    border: 5px solid var(--brand-blue);
  }
  .card-back .wordmark {
    color: var(--brand-blue); font-weight: 400; font-size: 32px; letter-spacing: -0.3px;
  }
  .card-back .details {
    position: absolute; left: 0; top: 142px; width: 100%; height: 166px;
    background: var(--brand-blue); color: var(--ink-light);
    display: flex; padding: 26px 30px 0 30px; gap: 26px;
  }
  .person {
    flex: 0 0 250px; text-align: right;
  }
  .person .name { font-weight: 700; font-size: 22px; line-height: 1.1; }
  .person .role { font-weight: 300; font-size: 15px; margin-top: 3px; }
  .person .address { font-weight: 300; font-size: 15px; margin-top: 12px; line-height: 1.35; }
  .contact-list { list-style: none; }
  .contact-list li {
    display: flex; align-items: center; gap: 8px;
    font-size: 13px; font-weight: 300; line-height: 1; margin-bottom: 9px;
  }
  .contact-list svg { width: 14px; height: 14px; flex: none; }
</style>
</head>
<body>
<main class="canvas">

  <section class="card card-front" aria-label="Business card front">
    <span class="mark-circle" aria-hidden="true"></span>
    <span class="wordmark">Verdel Wellworks</span>
  </section>

  <section class="card card-back" aria-label="Business card back">
    <header class="header">
      <span class="mark-circle" aria-hidden="true"></span>
      <span class="wordmark">Verdel Wellworks</span>
    </header>
    <div class="details">
      <div class="person">
        <p class="name">Dorvane Pike</p>
        <p class="role">Managing Director</p>
        <p class="address">1234, Harbour Lane West<br>Toronto, M5V 2K1</p>
      </div>
      <ul class="contact-list">
        <li>
          <svg viewBox="0 0 14 14" aria-hidden="true"><rect width="14" height="14" rx="2" fill="#fff"/><path d="M4 3.5h2l.8 2-1.2.9a5 5 0 0 0 2 2l.9-1.2 2 .8v2c0 .5-.4.8-.9.8A7 7 0 0 1 3.2 4.4c0-.5.3-.9.8-.9z" fill="#0b86f2"/></svg>
          555-204-7718
        </li>
        <li>
          <svg viewBox="0 0 14 14" aria-hidden="true"><rect width="14" height="14" rx="2" fill="#fff"/><rect x="4.2" y="2.5" width="5.6" height="9" rx="1" fill="#0b86f2"/><rect x="5.2" y="3.6" width="3.6" height="5.6" fill="#fff"/></svg>
          555-204-7719
        </li>
        <li>
          <svg viewBox="0 0 14 14" aria-hidden="true"><rect width="14" height="14" rx="2" fill="#fff"/><rect x="2.5" y="4" width="9" height="6" fill="#0b86f2"/><path d="M2.5 4l4.5 3.5L11.5 4" stroke="#fff" stroke-width="1" fill="none"/></svg>
          info@verdelwellworks.example
        </li>
        <li>
          <svg viewBox="0 0 14 14" aria-hidden="true"><rect width="14" height="14" rx="2" fill="#fff"/><circle cx="7" cy="7" r="4" fill="none" stroke="#0b86f2" stroke-width="1.2"/><path d="M3 7h8M7 3c-2 2.4-2 5.6 0 8M7 3c2 2.4 2 5.6 0 8" stroke="#0b86f2" stroke-width="0.9" fill="none"/></svg>
          www.verdelwellworks.example
        </li>
      </ul>
    </div>
  </section>

</main>
</body>
</html>
```